Weightloss company needs Business Card

We want a business card that is clean and professional, yet portrays that we are a friendly, innovative, and versatile program designed to fit the needs of our clients.
I would like there to be 2 sides, one side having an appointment card, and the other side containing the logo and business information. There can be decorations on both sides. The logo is attached.

Target Market(s)

Men and women 40-60

Industry/Entity Type

Business

Contact Information for Business Card

Font styles to use
Sans Serif

Requirements
Must have
• The logo, space for business information
Nice to have
• The colors in the logo
Should not have
• No pictures of people or food

```html
<!DOCTYPE html>
<html lang="en">
<head>
<meta charset="utf-8">
<title>Brightpath Weightloss – Business Card</title>
<link rel="stylesheet" href="https://fonts.googleapis.com/css2?family=Open+Sans:wght@400;600;700;800&display=swap">
<style>
  :root {
    --backdrop: #ebe7e2;
    --kraft-light: #d2b48f;
    --kraft: #c3a077;
    --kraft-dark: #b48f66;
    --ink: #121212;
    --paper: #ffffff;
  }
  * { box-sizing: border-box; margin: 0; padding: 0; }
  html, body {
    width: 1200px; height: 900px; overflow: hidden;
    background: var(--backdrop);
    font-family: "Open Sans", Arial, sans-serif;
    color: var(--ink);
  }
  .canvas { position: relative; width: 1200px; height: 900px; }

  .card {
    position: absolute;
    height: 342px;
    background: linear-gradient(135deg, var(--kraft-light) 0%, var(--kraft) 55%, var(--kraft-dark) 100%);
    box-shadow: 0 6px 18px rgba(0,0,0,0.18);
    overflow: hidden;
  }
  .card--front { left: 238px; top: 62px; width: 555px; }
  .card--appointment { left: 457px; top: 519px; width: 560px; }

  .brand {
    position: absolute; left: 0; right: 0;
    text-align: center;
    font-weight: 800;
    line-height: 1;
    letter-spacing: -0.5px;
  }
  .brand__name { display: block; font-size: 34px; }
  .brand__tag { display: block; font-size: 24px; margin-top: 2px; }
  .card--front .brand { top: 70px; }
  .card--appointment .brand { top: 60px; }

  .contact-holder {
    position: absolute; top: 190px; left: 0; right: 0;
    text-align: center;
  }
  .holder__name { font-size: 18px; font-weight: 600; }
  .holder__role { font-size: 14px; margin-top: 1px; }
  .contact-list {
    list-style: none;
    margin-top: 20px;
    font-size: 14.5px;
    line-height: 20px;
  }
  .contact-list li { display: flex; justify-content: center; align-items: center; gap: 7px; }
  .contact-list svg { width: 12px; height: 12px; fill: var(--ink); }

  .appointment__heading {
    position: absolute; top: 158px; left: 0; right: 0;
    text-align: center; font-size: 21px; font-weight: 600;
  }
  .appointment__form {
    position: absolute; left: 0; right: 0; bottom: 0; height: 138px;
    background: var(--paper);
    padding: 20px 100px 0;
    font-size: 13.5px; font-weight: 600;
  }
  .form-row { display: flex; align-items: flex-end; height: 22px; margin-bottom: 21px; }
  .form-row__line {
    flex: 1; border-bottom: 2px dotted var(--ink);
    margin: 0 2px 4px 4px;
  }
  .form-row__line--short { flex: 0 0 165px; }
  .form-row__line--time { flex: 0 0 110px; }
  .appointment__notice { text-align: center; margin-top: -2px; }
</style>
</head>
<body>
<main class="canvas">

  <section class="card card--front" aria-label="Business card, contact side">
    <div class="brand">
      <span class="brand__name">Brightpath</span>
      <span class="brand__tag">Weightloss</span>
    </div>
    <div class="contact-holder">
      <p class="holder__name">Daniel Morgan</p>
      <p class="holder__role">Managing Director</p>
      <ul class="contact-list">
        <li>
          <svg viewBox="0 0 24 24" aria-hidden="true"><path d="M6.6 10.8a15.1 15.1 0 0 0 6.6 6.6l2.2-2.2c.3-.3.7-.4 1-.2 1.1.4 2.3.6 3.6.6.6 0 1 .4 1 1V20c0 .6-.4 1-1 1A17 17 0 0 1 3 4c0-.6.4-1 1-1h3.5c.6 0 1 .4 1 1 0 1.3.2 2.5.6 3.6.1.3 0 .7-.2 1z"/></svg>
          044-987 654 321
        </li>
        <li>
          <svg viewBox="0 0 24 24" aria-hidden="true"><path d="M2 5h20v14H2z M2 5l10 8 10-8" fill="none" stroke="#121212" stroke-width="0"/><path d="M2 6.5V19h20V6.5l-10 7.5z"/><path d="M2 5h20l-10 7.5z"/></svg>
          hello@brightpath.com
        </li>
        <li>
          <svg viewBox="0 0 24 24" aria-hidden="true"><circle cx="12" cy="12" r="10"/><path d="M2 12h20M12 2c3 3 3 17 0 20M12 2c-3 3-3 17 0 20" stroke="#c3a077" stroke-width="1.6" fill="none"/></svg>
          www.brightpathweight.com
        </li>
      </ul>
    </div>
  </section>

  <section class="card card--appointment" aria-label="Business card, appointment side">
    <div class="brand">
      <span class="brand__name">Brightpath</span>
      <span class="brand__tag">Weightloss</span>
    </div>
    <h2 class="appointment__heading">Your Next Appointment is</h2>
    <div class="appointment__form">
      <div class="form-row"><span>Name:</span><span class="form-row__line"></span></div>
      <div class="form-row">
        <span>Date:</span><span class="form-row__line form-row__line--short"></span>
        <span>Time:</span><span class="form-row__line form-row__line--time"></span>
      </div>
      <p class="appointment__notice">If unable to keep appointment,&nbsp; kindly give 24hrs notice.</p>
    </div>
  </section>

</main>
</body>
</html>
```